Consulting company business cards

We have a base design, but would be willing to update. We have a new logo/"tag" that needs to be added. Current business card design is attached for reference into our "style."

Industry/Entity Type

Business

Contact Information for Business Card

Should contain name and title, office number, mobile number if appropriate, e-mail, website, physical address, and company logo.

Font styles to use
Other font styles liked:
• See current card design on KorvandBCard

Colors
0455a3
85acd3
aaaaaa

Requirements
Must have
• Our colors are navy blue, gray, and a lighter blue
Nice to have
• Design that I can easily drop in new names/titles as we hire employees.

```html
<!DOCTYPE html>
<html lang="en">
<head>
<meta charset="utf-8">
<title>Brenlow Business Cards</title>
<link href="https://fonts.googleapis.com/css2?family=Oswald:wght@600&family=Questrial&display=swap" rel="stylesheet">
<style>
  :root {
    --navy: #0d3a5c;
    --navy-deep: #0a2f4c;
    --ink: #123a5e;
    --sky: #5aa7c7;
    --sky-soft: #85acd3;
    --cream: #efede2;
    --gray: #aaaaaa;
    --text: #3c3c3c;
    --page: #e4e6e8;
  }
  * { box-sizing: border-box; margin: 0; padding: 0; }
  html, body { width: 1200px; height: 786px; overflow: hidden; }
  body {
    background: var(--page);
    font-family: "Questrial", sans-serif;
    display: flex;
    align-items: center;
    justify-content: center;
    gap: 48px;
  }
  .card {
    position: relative;
    width: 540px;
    height: 309px;
    border-radius: 18px;
    overflow: hidden;
    box-shadow: 0 8px 22px rgba(0,0,0,0.18);
  }
  /* Front */
  .card-front { background: var(--cream); }
  .card-front .wave {
    position: absolute; left: 0; bottom: 0; width: 100%; height: 100%;
  }
  .brand {
    position: absolute;
    display: flex; flex-direction: column;
  }
  .brand-row { display: flex; align-items: center; gap: 10px; }
  .brand-name {
    font-family: "Oswald", sans-serif;
    font-weight: 600;
    letter-spacing: 2px;
    line-height: 1;
  }
  .brand-dot { border-radius: 50%; background: var(--sky); }
  .brand-tag {
    font-size: 9px;
    letter-spacing: 2.2px;
    text-transform: uppercase;
    margin-top: 5px;
  }
  .card-front .brand { left: 38px; top: 58px; }
  .card-front .brand-name { font-size: 50px; color: var(--ink); }
  .card-front .brand-dot { width: 26px; height: 26px; }
  .card-front .brand-tag { color: #6a6a6a; }
  .divider {
    position: absolute; left: 292px; top: 70px; width: 1px; height: 170px;
    background: #cfccbf;
  }
  .contact { position: absolute; left: 312px; top: 66px; color: var(--text); }
  .person-name {
    font-family: "Oswald", sans-serif; font-weight: 600;
    font-size: 20px; letter-spacing: 1px; color: var(--ink); text-transform: uppercase;
  }
  .person-title { font-size: 15px; margin-bottom: 10px; }
  .contact-list { list-style: none; font-size: 13px; line-height: 19px; }
  .contact-list li { display: flex; align-items: center; gap: 7px; }
  .contact-list .icon { width: 13px; height: 13px; flex: none; }
  .contact-list .plain { padding-left: 20px; }
  .address { margin-top: 8px; font-size: 13px; line-height: 17px; }
  /* Back */
  .card-back {
    background: radial-gradient(ellipse at 70% 80%, #124468 0%, var(--navy) 55%, var(--navy-deep) 100%);
    display: flex; align-items: center; justify-content: center;
  }
  .card-back .brand { position: static; }
  .card-back .brand-name { font-size: 54px; color: var(--cream); }
  .card-back .brand-dot { width: 28px; height: 28px; }
  .card-back .brand-tag { color: var(--sky-soft); }
</style>
</head>
<body>
  <section class="card card-front" aria-label="Business card front">
    <svg class="wave" viewBox="0 0 540 309" preserveAspectRatio="none" aria-hidden="true">
      <path d="M0 150 C 90 200, 200 250, 300 309 L 0 309 Z" fill="var(--navy)"/>
      <path d="M0 150 C 90 200, 200 250, 300 309 L 282 309 C 190 258, 90 210, 0 168 Z" fill="var(--cream)"/>
      <path d="M0 128 C 100 185, 210 240, 318 309 L 300 309 C 200 250, 90 200, 0 150 Z" fill="var(--sky)"/>
    </svg>
    <div class="brand">
      <div class="brand-row">
        <span class="brand-name">BRENLOW</span>
        <span class="brand-dot"></span>
      </div>
      <span class="brand-tag">A Cloud Consulting Company</span>
    </div>
    <div class="divider"></div>
    <div class="contact">
      <h1 class="person-name">Dana Korvand</h1>
      <p class="person-title">Office Manager</p>
      <ul class="contact-list">
        <li><svg class="icon" viewBox="0 0 13 13"><rect width="13" height="13" rx="2" fill="var(--sky)"/><path d="M4 3 L5.5 3 L6 5 L5 5.8 C5.5 7 6 7.5 7.2 8 L8 7 L10 7.5 L10 9 C7 9.5 3.5 6 4 3 Z" fill="#fff"/></svg>555.014.2910</li>
        <li><svg class="icon" viewBox="0 0 13 13"><rect width="13" height="13" rx="2" fill="var(--sky)"/><rect x="4.5" y="2.5" width="4" height="8" rx="0.8" fill="#fff"/></svg>555.014.2971</li>
        <li><svg class="icon" viewBox="0 0 13 13"><rect width="13" height="13" rx="2" fill="var(--sky)"/><rect x="2.5" y="4" width="8" height="5.5" fill="#fff"/><path d="M2.5 4 L6.5 7 L10.5 4" stroke="var(--sky)" fill="none"/></svg>dkorvand@brenlowtech.com</li>
        <li class="plain">www.brenlowtech.com</li>
      </ul>
      <p class="address">1187 W 41st. St Ashford<br>Indiana 46099</p>
    </div>
  </section>

  <section class="card card-back" aria-label="Business card back">
    <div class="brand">
      <div class="brand-row">
        <span class="brand-name">BRENLOW</span>
        <span class="brand-dot"></span>
      </div>
      <span class="brand-tag">A Cloud Consulting Company</span>
    </div>
  </section>
</body>
</html>
```